Silver Bloom Marisol's Cleaning Service Business Cards Project

A business card with all contact details with logo design on there (already have a logo) eye catching Logo and contact info on one side, full logo on the back, must target upper class residential and corporate companies, fitness companies, still keep it on the feminine side of things , must look elegant

Target Market(s)

Upper class homes and corporate companies

Industry/Entity Type

Cleaning Service

Contact Information for Business Card

Name: Marisol Quenby
Position: Director
ABN: 31647209853
Email: marisolssilvercleaning@tidymail.example
Number: 0417906354

Font styles to use
Decorative

Colors

Designer to choose colors to be used in the design.

Requirements
Must have
• Available Sydney Wide, contact info and logo on one side, full logo on the back
Nice to have
• Professional appearance
Should not have
• Cheap advert looking stuff

```html
<!DOCTYPE html>
<html lang="en">
<head>
<meta charset="utf-8">
<title>Silver Bloom – Business Cards</title>
<link rel="stylesheet" href="https://fonts.googleapis.com/css2?family=Roboto:wght@400;500&family=Roboto+Condensed:wght@700&display=swap">
<style>
  :root {
    --backdrop: #e9e6e1;
    --ink-black: #1b1c1e;
    --paper: #ffffff;
    --aqua: #2ee6dc;
    --aqua-pale: #9ff5f1;
    --brand-teal: #33d9cf;
    --text-grey: #555555;
    --text-dark: #4a4a4a;
  }
  * { margin: 0; padding: 0; box-sizing: border-box; }
  html, body { width: 1200px; height: 960px; overflow: hidden; }
  body { background: var(--backdrop); position: relative; font-family: "Roboto", sans-serif; }

  .card { position: absolute; width: 600px; height: 342px; overflow: hidden; box-shadow: 0 3px 8px rgba(0,0,0,.25); }
  .card--front { left: 314px; top: 113px; background: var(--paper); }
  .card--back  { left: 311px; top: 472px; background: var(--aqua); }

  .card__art { position: absolute; inset: 0; }
  .ornament { position: absolute; }

  .brand-name { position: absolute; text-align: center; font-family: "Roboto", sans-serif; font-weight: 500; line-height: 1.3; }
  .card--front .brand-name { left: 40px; width: 210px; top: 92px; font-size: 15px; color: var(--brand-teal); }
  .card--back .brand-name { left: 150px; width: 300px; top: 96px; font-size: 22px; color: var(--paper); }

  .contact { position: absolute; right: 17px; top: 180px; text-align: right; color: var(--text-grey); }
  .contact__name { font-family: "Roboto Condensed", sans-serif; font-weight: 700; font-size: 20px; color: var(--text-dark); line-height: 1; }
  .contact__role { font-weight: 500; font-size: 14px; letter-spacing: .5px; margin-top: 4px; }
  .contact__abn { font-size: 14px; margin-top: 15px; }
  .contact__list { list-style: none; margin-top: 9px; font-size: 14px; }
  .contact__item { display: flex; justify-content: flex-end; align-items: center; gap: 6px; height: 19.5px; }
  .contact__icon { width: 12px; height: 12px; fill: var(--aqua); flex: none; }

  .web { position: absolute; left: 0; width: 600px; top: 288px; text-align: center; color: var(--paper); font-size: 14px; letter-spacing: 3.6px; }
</style>
</head>
<body>

<section class="card card--front" aria-label="Business card front">
  <svg class="card__art" width="600" height="342" viewBox="0 0 600 342" aria-hidden="true">
    <path d="M0 0 H300 C262 70 258 150 282 220 C298 270 290 315 262 342 H0 Z" fill="var(--ink-black)"/>
  </svg>
  <svg class="ornament" style="left:205px;top:0" width="215" height="342" viewBox="0 0 215 342" role="img" aria-label="Flowing floral swirl ornament along the card divide">
    <defs>
      <linearGradient id="swirlFill" x1="0" y1="0" x2="1" y2="1">
        <stop offset="0" stop-color="#9ff5f1" stop-opacity=".5"/>
        <stop offset="1" stop-color="#9ff5f1" stop-opacity=".8"/>
      </linearGradient>
    </defs>
    <path d="M120 0 H150 C200 40 215 130 190 180 C160 220 110 200 95 260 C88 300 90 325 80 342 H40 C15 320 5 290 20 260 C50 230 70 200 72 160 C74 100 95 50 120 0 Z" fill="url(#swirlFill)"/>
  </svg>

  <svg class="ornament" style="left:48px;top:150px" width="190" height="36" viewBox="0 0 190 36" role="img" aria-label="Scrolling floral flourish">
    <rect width="190" height="36" rx="18" fill="var(--aqua-pale)" opacity=".3"/>
  </svg>
  <div class="brand-name">Silver Bloom Marisol's Cleaning Service</div>

  <div class="contact">
    <div class="contact__name">MARISOL QUENBY</div>
    <div class="contact__role">DIRECTOR</div>
    <div class="contact__abn">ABN: 31647209853</div>
    <ul class="contact__list">
      <li class="contact__item">0417906354
        <svg class="contact__icon" viewBox="0 0 24 24" aria-hidden="true"><path d="M6.6 10.8a15 15 0 0 0 6.6 6.6l2.2-2.2a1 1 0 0 1 1-.25 11.4 11.4 0 0 0 3.6.57 1 1 0 0 1 1 1V20a1 1 0 0 1-1 1A17 17 0 0 1 3 4a1 1 0 0 1 1-1h3.5a1 1 0 0 1 1 1c0 1.25.2 2.45.57 3.57a1 1 0 0 1-.25 1z"/></svg>
      </li>
      <li class="contact__item">marisolssilvercleaning@tidymail.example
        <svg class="contact__icon" viewBox="0 0 24 24" aria-hidden="true"><path d="M2 5h20v14H2z M2 5l10 8 10-8" fill="var(--aqua)" stroke="#fff" stroke-width="1.6"/></svg>
      </li>
      <li class="contact__item">www.silverbloomclean.example
        <svg class="contact__icon" viewBox="0 0 24 24" aria-hidden="true"><circle cx="12" cy="12" r="11"/><path d="M6 8c3 0 4 2 3 4s2 3 2 6M15 4c0 3 2 4 5 4M14 14c2 0 3 2 4 4" stroke="#fff" stroke-width="1.6" fill="none"/></svg>
      </li>
    </ul>
  </div>
</section>

<section class="card card--back" aria-label="Business card back">
  <div class="brand-name">Silver Bloom Marisol's Cleaning Service</div>
  <svg class="ornament" style="left:145px;top:182px" width="300" height="66" viewBox="0 0 300 66" role="img" aria-label="Symmetrical scrolling floral flourish">
    <rect width="300" height="66" rx="33" fill="#ffffff" opacity=".28"/>
  </svg>
  <div class="web">www.silverbloomclean.example</div>
</section>

</body>
</html>
```